zorvan lumet website design

An IT support and IT Security Company - just use dummy text for now for the design. Examples of sites we like the looks and feel of but need it more professional feel are like: www.kelbrovault.uk.com , www.pravok.co.uk, www.quenthardy.com/professional/, www.vur.com, www.melvish.com,

Best to message me if you have any questions

Target Market(s)

small to medium UK based companies that require IT support services

Industry/Entity Type

It Company

Contact Information for Business Card

use dummy name, telephone and email for now, will provide details later.

Logo Text

zorvan lumet (and then below the logo it should say "your IT, networks and security partner")

Coding

Coded - Design and coding required

Number of Pages Required

5+ page

Colors

Designer to choose colors to be used in the design.

Requirements
Must have
• must be professional, yet simple and clear that this is a serious IT support and IT security company.
Nice to have
• 1)The website homepage must have professional quality pictures of IT support or London city skyline or any picture that projects friendly business partners, professionalism and ready to serve.
• 2) Home page needs to include tabs for following pages 'Services' , 'About Us' , 'Contact Us' 'Home'
• 3) Website built customised using wordpress is ideal and easy for us to manage.
• more room for boxed options from homepage (with pic or image in background)
Should not have
• no checkout trolleys or payment options.

```html
<!DOCTYPE html>
<html lang="en">
<head>
<meta charset="utf-8">
<title>Zorvan Lumet – Business Card</title>
<link rel="stylesheet" href="https://fonts.googleapis.com/css2?family=Ubuntu:wght@400;500;700&display=swap">
<style>
  :root {
    --page: #ffffff;
    --sky: #45b9e9;
    --tangerine: #f48b46;
    --ink: #1c1c1c;
    --white: #ffffff;
    --shadow: rgba(0, 0, 0, 0.12);
  }
  * { box-sizing: border-box; margin: 0; padding: 0; }
  html, body {
    width: 668px; height: 1200px; overflow: hidden;
    background: var(--page);
    font-family: "Ubuntu", sans-serif;
  }
  .canvas { position: relative; width: 668px; height: 1200px; }
  .card {
    position: absolute; left: 95px; width: 497px; height: 270px;
    overflow: hidden; box-shadow: 0 1px 6px var(--shadow);
  }
  .card--front { top: 305px; background: var(--white); }
  .card--back { top: 625px; }

  .front-panel { position: absolute; inset: 0; }
  .holder { position: absolute; left: 28px; top: 22px; color: var(--white); }
  .holder__name { font-size: 12px; font-weight: 500; letter-spacing: 0.2px; }
  .holder__role { font-size: 9.5px; margin-top: 5px; }
  .panel-name {
    position: absolute; left: 20px; top: 122px; width: 200px; text-align: center;
    color: var(--white); font-weight: 700; font-size: 20px; letter-spacing: 0.5px;
    text-transform: uppercase;
  }

  .brand { position: absolute; left: 290px; top: 72px; width: 190px; text-align: center; }
  .brand__name {
    font-weight: 700; font-size: 21px; color: var(--sky);
    text-transform: uppercase; letter-spacing: 0.3px; line-height: 1;
  }
  .brand__tagline {
    font-weight: 700; font-size: 6.4px; color: var(--ink);
    text-transform: uppercase; margin-top: 5px; letter-spacing: 0.1px;
  }

  .contacts { position: absolute; left: 275px; top: 148px; list-style: none; }
  .contact { display: flex; align-items: center; height: 29px; margin-bottom: 7px; }
  .contact__icon { width: 29px; height: 29px; flex: none; }
  .contact__text {
    margin-left: 9px; font-size: 11.5px; font-weight: 500; color: var(--ink); line-height: 1.3;
  }

  .back-fill { position: absolute; inset: 0; }
  .back-brand {
    position: absolute; left: 0; right: 0; top: 140px; text-align: center; color: var(--white);
  }
  .back-brand__name {
    font-weight: 700; font-size: 28px; text-transform: uppercase; letter-spacing: 0.5px; line-height: 1;
  }
  .back-brand__tagline {
    font-weight: 700; font-size: 6.6px; text-transform: uppercase; margin-top: 6px;
  }
  .back-url {
    position: absolute; left: 0; right: 0; top: 232px; text-align: center;
    color: var(--white); font-size: 10.5px; font-weight: 500;
  }
</style>
</head>
<body>
<main class="canvas">

  <section class="card card--front" aria-label="Business card front">
    <svg class="front-panel" width="497" height="270" viewBox="0 0 497 270" role="img"
         aria-label="Blue panel with circuit-board pattern">
      <polygon points="0,0 269,0 215,270 0,270" fill="var(--sky)"/>
    </svg>
    <div class="holder">
      <p class="holder__name">Tomas Ardel Ruhl</p>
      <p class="holder__role">Director</p>
    </div>
    <p class="panel-name">zorvan lumet</p>

    <div class="brand">
      <p class="brand__name">zorvan lumet</p>
      <p class="brand__tagline">Your IT, networks and security partner</p>
    </div>

    <ul class="contacts">
      <li class="contact">
        <svg class="contact__icon" viewBox="0 0 29 29" aria-hidden="true">
          <circle cx="14.5" cy="14.5" r="14.5" fill="var(--tangerine)"/>
          <path d="M14.5 7.5a5 5 0 0 0-5 5c0 3.6 5 9 5 9s5-5.4 5-9a5 5 0 0 0-5-5z" fill="var(--white)"/>
          <circle cx="14.5" cy="12.5" r="1.8" fill="var(--tangerine)"/>
        </svg>
        <span class="contact__text">Lorem Ipsum Dolor Sit Amet<br>Consectetore</span>
      </li>
      <li class="contact">
        <svg class="contact__icon" viewBox="0 0 29 29" aria-hidden="true">
          <circle cx="14.5" cy="14.5" r="14.5" fill="var(--tangerine)"/>
          <path d="M8.5 12c0-2 2.7-3 6-3s6 1 6 3v1h-3v-1.4h-6V13h-3z" fill="var(--white)"/>
          <rect x="9.5" y="14" width="10" height="6.5" rx="1" fill="var(--white)"/>
          <circle cx="14.5" cy="17.2" r="1.5" fill="var(--tangerine)"/>
        </svg>
        <span class="contact__text">+00 1 2345 6789</span>
      </li>
      <li class="contact">
        <svg class="contact__icon" viewBox="0 0 29 29" aria-hidden="true">
          <circle cx="14.5" cy="14.5" r="14.5" fill="var(--tangerine)"/>
          <rect x="8.5" y="10" width="12" height="9" rx="1" fill="var(--white)"/>
          <path d="M8.8 10.5l5.7 4.5 5.7-4.5" fill="none" stroke="var(--tangerine)" stroke-width="1.2"/>
        </svg>
        <span class="contact__text">info@zorvanlumet.com</span>
      </li>
    </ul>
  </section>

  <section class="card card--back" aria-label="Business card back">
    <svg class="back-fill" width="497" height="270" viewBox="0 0 497 270" role="img"
         aria-label="Orange background with circuit-board pattern">
      <rect width="497" height="270" fill="var(--tangerine)"/>
    </svg>
    <div class="back-brand">
      <p class="back-brand__name">zorvan lumet</p>
      <p class="back-brand__tagline">Your IT, networks and security partner</p>
    </div>
    <p class="back-url">www.zorvanlumet.com</p>
  </section>

</main>
</body>
</html>
```